Tech business card design

We need an amazing business card design for our new business 'Pexla' a marketing tech startup based in Sydney, Australia. We provide an online marketplace for businesses to search and buy advertising media, connect with service providers and learn more about marketing. We wish to communicate 'cool tech', reliability and professionalism and design based around our logo.

Target Market(s)

Business Owners

Contact Information for Business Card

Name
Position
Email Address
Website
Phone Number

Font styles to use
Other font styles liked:
• Avenir & Avenir Next

Colors

Designer to choose colors to be used in the design.

```html
<!DOCTYPE html>
<html lang="en">
<head>
<meta charset="UTF-8">
<title>Pexla Business Card</title>
<link href="https://fonts.googleapis.com/css2?family=Nunito+Sans:wght@400;600;800&display=swap" rel="stylesheet">
<style>
  :root {
    --backdrop: #ececec;
    --ink: #221f45;
    --paper: #ffffff;
    --paper-text: #ffffff;
  }
  * { margin: 0; padding: 0; box-sizing: border-box; }
  html, body {
    width: 1200px;
    height: 800px;
    overflow: hidden;
    background: var(--backdrop);
    font-family: "Nunito Sans", Arial, sans-serif;
  }
  .canvas {
    position: relative;
    width: 1200px;
    height: 800px;
  }
  .card {
    position: absolute;
    top: 278px;
    width: 420px;
    height: 240px;
    overflow: hidden;
  }
  .card--front {
    left: 141px;
    background: var(--ink);
  }
  .card--back {
    left: 638px;
    background: var(--paper);
  }
  .wordmark {
    position: absolute;
    font-weight: 800;
    letter-spacing: -0.02em;
    line-height: 1;
  }
  .wordmark sup {
    font-size: 0.11em;
    font-weight: 800;
    letter-spacing: 0;
    vertical-align: baseline;
    margin-left: 4px;
  }
  .card--front .wordmark {
    left: 0;
    right: 0;
    top: 78px;
    text-align: center;
    font-size: 96px;
    color: var(--paper-text);
  }
  .card--back .wordmark {
    left: 28px;
    top: 38px;
    font-size: 54px;
    color: var(--ink);
  }
  .identity {
    position: absolute;
    left: 216px;
    top: 52px;
    color: var(--ink);
    text-transform: uppercase;
    line-height: 1.05;
  }
  .identity__name {
    font-size: 19px;
    font-weight: 800;
    letter-spacing: 0.02em;
  }
  .identity__role {
    font-size: 13px;
    font-weight: 600;
    letter-spacing: 0.02em;
  }
  .contacts {
    position: absolute;
    left: 200px;
    right: 0;
    top: 104px;
    list-style: none;
  }
  .contact {
    display: flex;
    align-items: center;
    height: 28px;
    margin-bottom: 10px;
    padding-left: 14px;
    background: var(--ink);
    border-radius: 14px 0 0 14px;
    color: var(--paper-text);
    font-size: 13px;
    font-weight: 600;
    letter-spacing: 0.02em;
  }
  .contact__icon {
    width: 14px;
    height: 14px;
    margin-right: 12px;
    flex: none;
  }
</style>
</head>
<body>
<main class="canvas">
  <section class="card card--front">
    <div class="wordmark">Pexla<sup>TM</sup></div>
  </section>

  <section class="card card--back">
    <div class="wordmark">Pexla<sup>TM</sup></div>
    <div class="identity">
      <p class="identity__name">Jordan Hale</p>
      <p class="identity__role">General Manager</p>
    </div>
    <ul class="contacts">
      <li class="contact">
        <svg class="contact__icon" viewBox="0 0 14 14" aria-hidden="true">
          <circle cx="7" cy="7" r="7" fill="#fff"/>
          <path d="M4.3 3.6l1.3-.3.8 1.8-.8.6c.4.9 1.1 1.6 2 2l.6-.8 1.8.8-.3 1.3c-2.9.1-5.5-2.5-5.4-5.4z" fill="#221f45"/>
        </svg>
        012 345 6789
      </li>
      <li class="contact">
        <svg class="contact__icon" viewBox="0 0 14 14" aria-hidden="true">
          <rect x="0.5" y="2.5" width="13" height="9" rx="1" fill="#fff"/>
          <path d="M1 3.2l6 4.3 6-4.3" fill="none" stroke="#221f45" stroke-width="1.2"/>
        </svg>
        your@email.com
      </li>
      <li class="contact">
        <svg class="contact__icon" viewBox="0 0 14 14" aria-hidden="true">
          <circle cx="7" cy="7" r="6.2" fill="none" stroke="#fff" stroke-width="1.2"/>
          <ellipse cx="7" cy="7" rx="2.6" ry="6.2" fill="none" stroke="#fff" stroke-width="1"/>
          <path d="M1 7h12M2 4h10M2 10h10" stroke="#fff" stroke-width="1"/>
        </svg>
        www.website.com
      </li>
    </ul>
  </section>
</main>
</body>
</html>
```